Marlow Dermal Studio - Business Banner with Brand Elements

Design:
• We would like to get a creative design for a wide banner that will go outside our medical spa clinic location. We need a designer to make a simple yet colorful and high-quality design layout. We want this banner to be eye-catching and to communicate the services we offer at our business: Laser Hair Removal | Veluxin | Lip Filler.

Requirements:
• We would like the banner to include our companies information which is the following:

Logo
“Refresh Your Skin”
Laser Hair Removal | Veluxin | Lip Filler
(520) 867-2291
www.MarlowDermalStudio.com

Colors:
• Our business colors are orange, a hint of black and white, but mostly peach/orange tones. (Orange: #f78f20 , White: #ffffff)

Fonts:
• Josefins Sans Bold & Lato

Content and images can be located here:
https://files.quibbleshare.com/share/folders/7tKwP3zRa9_LmQxVb2nD5yHc04EeJuFs8?mode=viewing

The following will give you an idea of our brand presentation:
• Our website is: www.MarlowDermalStudio.com
• Our Pictavo; @marlowdermalstudio
• Our Lumora: www.lumoranet.com/marlowdermalstudio

Target Market(s)
• Women 25 - 45

Industry/Entity Type
• Beauty

```html
<!DOCTYPE html>
<html lang="en">
<head>
<meta charset="utf-8">
<title>Marlow Dermal Studio – Outdoor Banner</title>
<link href="https://fonts.googleapis.com/css2?family=Josefin+Sans:wght@400;600;700&display=swap" rel="stylesheet">
<style>
  :root {
    --backdrop: #303131;
    --peach: #f7a647;
    --charcoal: #383838;
    --white: #ffffff;
    --sky-top: #2fbcd8;
    --sky-mid: #8fd3e3;
    --sea: #1fb0b4;
  }
  html, body {
    margin: 0;
    padding: 0;
    width: 1200px;
    height: 1200px;
    overflow: hidden;
    background: var(--backdrop);
    font-family: "Josefin Sans", sans-serif;
  }
  .banner {
    position: absolute;
    left: 142px;
    top: 403px;
    width: 949px;
    height: 361px;
    background: var(--white);
    overflow: hidden;
    box-shadow: 3px 4px 8px rgba(0,0,0,0.45);
  }
  .banner-shapes {
    position: absolute;
    inset: 0;
  }
  .hero-photo {
    position: absolute;
    left: 0;
    top: 0;
    width: 590px;
    height: 253px;
  }
  .headline {
    position: absolute;
    left: 632px;
    top: 32px;
    margin: 0;
    color: var(--white);
    text-transform: uppercase;
    line-height: 1;
  }
  .headline-lead {
    display: block;
    font-weight: 600;
    font-size: 52px;
    letter-spacing: 1px;
    line-height: 48px;
  }
  .headline-key {
    display: block;
    font-weight: 700;
    font-size: 110px;
    line-height: 100px;
    margin-left: -6px;
    letter-spacing: -1px;
  }
  .service {
    position: absolute;
    display: flex;
    align-items: center;
    top: 311px;
    transform: translateY(-50%);
    white-space: nowrap;
  }
  .service-icon {
    width: 52px;
    height: 52px;
    flex: none;
  }
  .service-label {
    color: var(--peach);
    font-weight: 700;
    font-size: 19px;
    line-height: 24px;
    text-transform: uppercase;
    letter-spacing: 0.4px;
    padding-top: 4px;
  }
  .service--laser { left: 27px; }
  .service--laser .service-label { margin-left: 18px; }
  .service--injectable { left: 238px; }
  .service--injectable .service-label { margin-left: 20px; }
  .service--lips { left: 414px; }
  .service--lips .service-label { margin-left: 22px; }
  .contact {
    position: absolute;
    display: flex;
    align-items: center;
    color: var(--white);
    font-weight: 600;
    transform: translateY(-50%);
    white-space: nowrap;
  }
  .contact-icon {
    width: 30px;
    height: 30px;
    flex: none;
  }
  .contact--phone { left: 630px; top: 284px; font-size: 20px; }
  .contact--phone .contact-text { margin-left: 12px; padding-top: 3px; }
  .contact--web { left: 617px; top: 324px; font-size: 18px; }
  .contact--web .contact-text { margin-left: 15px; padding-top: 3px; }
</style>
</head>
<body>
  <div class="banner">
    <svg class="banner-shapes" viewBox="0 0 949 361" width="949" height="361">
      <polygon points="590,0 949,0 949,253 543,253" fill="var(--peach)"/>
      <polygon points="663,235 949,235 949,361 618,361" fill="var(--charcoal)"/>
    </svg>

    <svg class="hero-photo" viewBox="0 0 590 253" width="590" height="253" role="img" aria-label="Photo of a smiling woman in a straw sun hat on a sunny beach with turquoise sea">
      <defs>
        <linearGradient id="beach" x1="0" y1="0" x2="0" y2="1">
          <stop offset="0" stop-color="var(--sky-top)"/>
          <stop offset="0.55" stop-color="var(--sky-mid)"/>
          <stop offset="0.62" stop-color="var(--sea)"/>
          <stop offset="1" stop-color="#b9e3e2"/>
        </linearGradient>
        <radialGradient id="figure" cx="0.5" cy="0.6" r="0.5">
          <stop offset="0" stop-color="#c8946a" stop-opacity="0.7"/>
          <stop offset="1" stop-color="#c8946a" stop-opacity="0"/>
        </radialGradient>
      </defs>
      <polygon points="0,0 580,0 534,253 0,253" fill="url(#beach)"/>
      <ellipse cx="300" cy="150" rx="150" ry="130" fill="url(#figure)"/>
    </svg>

    <h1 class="headline">
      <span class="headline-lead">Refresh</span>
      <span class="headline-lead">Your</span>
      <span class="headline-key">Skin</span>
    </h1>

    <div class="service service--laser">
      <svg class="service-icon" viewBox="0 0 52 52">
        <circle cx="26" cy="26" r="26" fill="var(--peach)"/>
        <g fill="none" stroke="var(--white)" stroke-width="1.6" stroke-linecap="round">
          <path d="M20 30 L34 14 L38 18 L24 34 Z"/>
          <path d="M29 26 C33 32 30 36 36 36"/>
          <path d="M17 33 L12 35 M16 37 L11 41 M19 38 L17 42 M14 30 L10 30"/>
        </g>
      </svg>
      <span class="service-label">Laser Hair<br>Removal</span>
    </div>

    <div class="service service--injectable">
      <svg class="service-icon" viewBox="0 0 52 52">
        <circle cx="26" cy="26" r="26" fill="var(--peach)"/>
        <g fill="none" stroke="var(--white)" stroke-width="1.6" stroke-linecap="round" stroke-linejoin="round">
          <path d="M14 18 L28 16 L32 22 L26 26 L16 24 Z"/>
          <path d="M30 26 L40 40"/>
          <path d="M28 28 L33 24 M37 36 L41 33"/>
          <path d="M40 40 L43 44"/>
        </g>
      </svg>
      <span class="service-label">Veluxin</span>
    </div>

    <div class="service service--lips">
      <svg class="service-icon" viewBox="0 0 52 52">
        <circle cx="26" cy="26" r="26" fill="var(--peach)"/>
        <g fill="none" stroke="var(--white)" stroke-width="1.6" stroke-linecap="round" stroke-linejoin="round">
          <path d="M10 24 C16 16 21 18 25 21 C29 18 34 16 40 24 C34 32 16 32 10 24 Z"/>
          <path d="M10 24 C18 26 32 26 40 24"/>
          <path d="M32 30 L42 42 M35 33 L38 30"/>
        </g>
      </svg>
      <span class="service-label">Lip Filler</span>
    </div>

    <div class="contact contact--phone">
      <svg class="contact-icon" viewBox="0 0 30 30">
        <circle cx="15" cy="15" r="14" fill="var(--white)"/>
        <circle cx="15" cy="15" r="11" fill="none" stroke="var(--peach)" stroke-width="1.6"/>
        <path d="M11 9 L13 9 L14 12 L12.5 13 C13.2 15 14.5 16.5 16.5 17.5 L17.5 16 L20.5 17 L20.5 19 C20 20.5 18 21 16 20 C13 18.5 11 16 10 13 C9.6 11 10 9.5 11 9 Z" fill="var(--peach)"/>
      </svg>
      <span class="contact-text">(520) 867-2291</span>
    </div>

    <div class="contact contact--web">
      <svg class="contact-icon" viewBox="0 0 30 30">
        <circle cx="15" cy="15" r="14" fill="var(--white)"/>
        <circle cx="15" cy="15" r="11" fill="none" stroke="var(--peach)" stroke-width="1.6"/>
        <g fill="none" stroke="var(--peach)" stroke-width="1.3">
          <circle cx="15" cy="15" r="7"/>
          <ellipse cx="15" cy="15" rx="3" ry="7"/>
          <path d="M8 15 H22 M9.5 11 H20.5 M9.5 19 H20.5"/>
        </g>
      </svg>
      <span class="contact-text">www.marlowdermalstudio.com</span>
    </div>
  </div>
</body>
</html>
```